Animal Eye Clinic needs a Business card

We are a new veterinary ophthalmology practice (Ridgeline Pet Vision Care) and we need a business card designed. We only see animal eyes - we are not a regular veterinary clinic. We already have a logo. We are looking for a professional, good looking business card to hand out to our clients. We are looking for something simple but professional and contemporary. Our logo is likely the only picture/graphic that needs to be on the card.
Updates

Contact Information for Business Card

Delia Vossman, BSc, DVM, MSc, DipACVO
Veterinary Ophthalmologist

Phone: 250.418.3927
Email: ridgelinepetvisioncare@mailbox-example.net
Website: ridgelinepetvisioncare-example.net
Address: 1874 Thornbury Rd
Kelowna, BC, V1X 4M9

Colors

Designer to choose colors to be used in the design.

Requirements
Must have
• Our logo (attached)

```html
<!DOCTYPE html>
<html lang="en">
<head>
<meta charset="utf-8">
<title>Ridgeline Pet Vision Care – Business Card</title>
<link href="https://fonts.googleapis.com/css2?family=Roboto:ital,wght@0,300;0,400;0,700;0,900;1,300;1,900&display=swap" rel="stylesheet">
<style>
  :root {
    --backdrop: #2f2f2f;
    --card: #585858;
    --teal: #1a9fb0;
    --white: #f2f2f2;
    --emboss-light: #626262;
    --emboss-mid: #555555;
    --emboss-dark: #4b4b4b;
    --emboss-edge: rgba(255,255,255,0.16);
  }
  * { box-sizing: border-box; margin: 0; padding: 0; }
  html, body {
    width: 1200px; height: 1125px; overflow: hidden;
    background: var(--backdrop);
    font-family: "Roboto", Arial, sans-serif;
  }
  .card {
    position: absolute; left: 160px;
    width: 880px; height: 503px;
    background: var(--card);
    border-bottom: 6px solid var(--teal);
    overflow: hidden;
  }
  .card--back { top: 40px; }
  .card--front { top: 582px; }

  .artwork {
    position: absolute;
    border-radius: 50%;
    background: linear-gradient(160deg, var(--emboss-light) 0%, var(--emboss-mid) 50%, var(--emboss-dark) 100%);
    box-shadow: inset 2px 2px 0 var(--emboss-edge), inset -2px -2px 3px rgba(0,0,0,0.18);
  }
  .card--back .artwork { left: 40px; top: 40px; width: 520px; height: 520px; }
  .card--front .artwork { left: 420px; top: 40px; width: 520px; height: 520px; }

  .back-name {
    position: absolute; left: 560px; top: 200px; width: 300px;
    font-weight: 700; font-size: 32px; line-height: 1.15;
    color: var(--teal); text-transform: uppercase; letter-spacing: 1px;
  }

  .brand {
    position: absolute; left: 56px; top: 42px;
    display: flex; align-items: center; gap: 14px;
  }
  .brand__dot { width: 44px; height: 44px; border-radius: 50%; background: var(--teal); flex: none; }
  .brand__name {
    font-weight: 700; font-size: 24px; color: var(--teal);
    text-transform: uppercase; letter-spacing: 1px;
  }

  .person { position: absolute; left: 56px; top: 124px; }
  .person__name {
    display: flex; align-items: center; gap: 14px;
    font-weight: 900; font-style: italic; font-size: 28px;
    color: var(--teal); letter-spacing: 3px; text-transform: uppercase;
  }
  .person__marker { width: 0; height: 0; border-top: 11px solid transparent; border-bottom: 11px solid transparent; border-left: 20px solid var(--teal); }
  .person__credentials { margin-left: 34px; font-weight: 300; font-style: italic; font-size: 20px; color: var(--teal); margin-top: 2px; }
  .person__title { margin-left: 34px; font-size: 21px; color: var(--white); margin-top: 2px; }

  .address { position: absolute; left: 90px; top: 240px; font-size: 21px; line-height: 1.4; color: var(--white); font-style: normal; }

  .contacts { position: absolute; left: 70px; top: 318px; list-style: none; font-size: 20px; color: var(--white); }
  .contacts li { display: flex; align-items: center; gap: 8px; line-height: 1.5; }
  .contacts svg { width: 16px; height: 16px; fill: var(--teal); flex: none; }
</style>
</head>
<body>

<section class="card card--back" aria-label="Business card back">
  <div class="artwork" role="img" aria-label="Blind-embossed illustration of a horse, dog and cat together"></div>
  <div class="back-name">Ridgeline Pet<br>Vision Care</div>
</section>

<section class="card card--front" aria-label="Business card front">
  <div class="artwork" role="img" aria-label="Blind-embossed illustration of a horse, dog and cat together"></div>

  <div class="brand">
    <span class="brand__dot"></span>
    <span class="brand__name">Ridgeline Pet Vision Care</span>
  </div>

  <div class="person">
    <div class="person__name"><span class="person__marker"></span>Delia Vossman</div>
    <div class="person__credentials">BSc, DVM, MSc, DipACVO</div>
    <div class="person__title">Veterinary Ophthalmologist</div>
  </div>

  <address class="address">1874 Thornbury Rd<br>Kelowna, BC, V1X 4M9</address>

  <ul class="contacts">
    <li><svg viewBox="0 0 16 16"><path d="M3.5 1l3 3-1.6 1.8a9 9 0 0 0 5.3 5.3L12 9.5l3 3-2 2.5C6.5 14.5 1.5 9.5 1 3z"/></svg>250.418.3927</li>
    <li><svg viewBox="0 0 16 16"><path d="M1 3h14v1.2L8 9 1 4.2z M1 5.8l7 4.8 7-4.8V13H1z"/></svg>ridgelinepetvisioncare@mailbox-example.net</li>
    <li><svg viewBox="0 0 16 16"><path d="M8 1a7 7 0 1 0 0 14A7 7 0 0 0 8 1zm0 1.5c.9 1 1.5 2.5 1.7 4.5H6.3C6.5 5 7.1 3.5 8 2.5zM2.6 7h2.2c.1-1.7.5-3.1 1.1-4.1A5.5 5.5 0 0 0 2.6 7zm8.6 0h2.2a5.5 5.5 0 0 0-3.3-4.1c.6 1 1 2.4 1.1 4.1zM2.6 9a5.5 5.5 0 0 0 3.3 4.1c-.6-1-1-2.4-1.1-4.1zm3.7 0c.2 2 .8 3.5 1.7 4.5.9-1 1.5-2.5 1.7-4.5zm4.9 0c-.1 1.7-.5 3.1-1.1 4.1A5.5 5.5 0 0 0 13.4 9z"/></svg>ridgelinepetvisioncare-example.net</li>
  </ul>
</section>

</body>
</html>
```